New website for concierge mobile medical service

new website for business:
WEBSITE REQUEST LIST:
Luxury product look.
Professional. Clean & simple, NO stock people photos. Graphics OK.
Black and white text.

```html
<!DOCTYPE html>
<html lang="en">
<head>
<meta charset="utf-8">
<title>Brightwell Health — Mobile Concierge Medicine</title>
<link href="https://fonts.googleapis.com/css2?family=Montserrat:wght@500;600;700&family=Open+Sans:wght@400;600&display=swap" rel="stylesheet">
<style>
:root{
  --navy:#0b2233;
  --teal-dark:#0e3e55;
  --cyan:#3ec3e8;
  --blue:#1f6fd1;
  --blue-link:#1a63c9;
  --ink:#141414;
  --body:#555b63;
  --tile-blue:#4fc1e9;
  --tile-steel:#6fa3d8;
  --tile-violet:#9d8fc9;
  --tile-sage:#b9d8a9;
  --mist:#eef8fc;
  --paper:#f2f3f5;
  --footer:#1b1e24;
  --white:#fff;
}
*{box-sizing:border-box;margin:0;padding:0}
html,body{width:1200px;height:5254px;overflow:hidden}
body{position:relative;background:var(--white);font-family:"Open Sans",sans-serif;color:var(--body)}
.abs{position:absolute}
h1,h2,h3,h4,.nav,.btn,.brand,.f-brand{font-family:"Montserrat",sans-serif}

/* hero */
.hero{left:0;top:0;width:1200px;height:690px;background:radial-gradient(ellipse at 70% 40%,#17607c 0%,var(--teal-dark) 45%,var(--navy) 100%)}
.hero-curve{left:0;top:600px;width:1200px;height:100px}
.nav{top:28px;left:88px;width:1030px;display:flex;align-items:center;font-size:16px;color:#fff}
.nav span{margin-right:48px}
.nav .active{color:var(--cyan)}
.nav .right{margin-left:auto;display:flex;align-items:center;gap:48px}
.nav .phone{font-weight:700;font-size:21px;display:flex;align-items:center;gap:10px}
.brand{left:500px;top:30px;width:200px;text-align:center;color:#fff;font-size:19px;font-weight:600;white-space:nowrap}
.hero-intro{left:90px;top:204px;width:530px;color:#fff;font-size:16px;line-height:28px}
.hero-accept{left:90px;top:276px;color:#fff;font-size:21px;font-family:"Montserrat",sans-serif;font-weight:500}
.hero-accept a{font-size:12px;color:#fff;text-decoration:underline;margin-left:6px}
.hero-lead{left:90px;top:324px;width:540px;color:#fff;font-size:24px;line-height:37px;font-weight:600}
.btn-hero{left:90px;top:466px;width:234px;height:54px;background:var(--cyan);color:#fff;font-weight:600;font-size:17px;display:flex;align-items:center;justify-content:center;border-radius:3px}
.hero-art{left:640px;top:96px;width:530px;height:520px;border-radius:40px;background:radial-gradient(circle at 55% 45%,#5fe2f5 0%,#1f9fc4 35%,rgba(14,62,85,0) 72%)}
.dots{left:562px;top:648px;display:flex;gap:10px}
.dots i{width:10px;height:10px;border-radius:50%;border:2px solid #fff}
.dots i:first-child{background:var(--cyan);border-color:var(--cyan)}

/* services */
.service{top:824px;width:314px}
.svc-head{display:flex;align-items:center;gap:14px}
.svc-icon{width:118px;height:118px;border-radius:50%;border:2px solid var(--cyan);flex:none}
.svc-head h3{font-size:22px;font-weight:500;color:var(--ink);line-height:30px}
.svc-text{margin-top:16px;font-size:15px;line-height:30.5px;text-align:justify}
.svc-list{list-style:none;margin-top:12px;font-size:15px;line-height:30.5px}
.svc-list li{padding-left:28px;position:relative}
.svc-list li:before{content:"»";position:absolute;left:2px;color:var(--cyan)}
.svc-link{margin-top:14px;font-family:"Montserrat",sans-serif;font-weight:700;font-size:15px;color:var(--blue-link)}

/* offer band */
.band{left:0;top:1360px;width:1200px;height:530px}
.band-text{left:0;top:1508px;width:1200px;text-align:center;color:#fff;font-size:17px}
.band-text p{margin-bottom:14px}
.band-text b{font-size:30px;font-family:"Montserrat",sans-serif;font-weight:600}
.prices{left:148px;top:1612px;color:#fff;font-size:17px;display:flex;gap:34px}
.prices b{font-size:19px;font-weight:600}
.btn-sub{left:483px;top:1680px;width:234px;height:52px;background:var(--blue);color:#fff;font-weight:600;font-size:17px;display:flex;align-items:center;justify-content:center;border-radius:3px}
.band-art{left:980px;top:1590px;width:220px;height:250px;border-radius:110px 0 0 40px;background:linear-gradient(150deg,#1a5fc4,#0e3f95)}

/* faq tiles */
.tile{width:500px;height:272px;color:#fff;padding:36px}
.tile h3{font-size:25px;font-weight:600;line-height:36px}
.tile a{position:absolute;bottom:38px;font-size:15px;color:#fff;text-decoration:underline}
.t1{left:90px;top:1976px;background:var(--tile-blue)}
.t2{left:610px;top:1976px;background:var(--tile-steel);text-align:right}
.t3{left:90px;top:2274px;background:var(--tile-violet);padding:40px 18px}
.t4{left:610px;top:2274px;background:var(--tile-sage);text-align:right;padding:40px 28px}
.t2 a,.t4 a{right:40px}
.ring{left:310px;top:1976px;width:580px;height:570px}

/* why */
.why-bg{left:0;top:2630px;width:1200px;height:1210px}
.why-title{left:0;top:2730px;width:1200px;text-align:center;font-size:35px;font-weight:600;color:var(--ink)}
.why-title span,.accent{color:var(--cyan)}
.why-art-a{left:80px;top:2830px;width:440px;height:360px;border-radius:30px;background:radial-gradient(circle at 50% 50%,#7fb6e6 0%,#c8e3f4 55%,rgba(238,248,252,0) 78%)}
.why-art-b{left:668px;top:3334px;width:532px;height:506px;background:linear-gradient(180deg,#d6ebf8 0%,#8cc2ee 55%,#3e8fe4 100%)}
.item{width:540px}
.item .num{position:absolute;left:0;top:0;width:42px;height:42px;border-radius:50%;border:2px solid var(--cyan);background:#fff;color:var(--cyan);font-weight:700;font-size:15px;display:flex;align-items:center;justify-content:center}
.item h4{margin-left:62px;font-size:16px;font-weight:500;color:var(--cyan);line-height:26px}
.item p{margin-left:62px;margin-top:6px;font-size:14px;line-height:28px;color:#4a4f55}

/* providers */
.prov-title{left:0;top:3918px;width:1200px;text-align:center;font-size:35px;font-weight:600;color:var(--ink)}
.prov{top:4002px;width:182px;text-align:center}
.prov .ph{width:182px;height:182px;border-radius:50%;background:radial-gradient(circle at 50% 40%,#9be0f4,#49b6dc)}
.prov p{margin-top:14px;font-family:"Montserrat",sans-serif;font-size:19px;color:var(--ink)}

/* newsletter */
.news-bg{left:0;top:4340px;width:1200px;height:450px}
.news-title{left:90px;top:4462px;font-size:35px;font-weight:700;color:var(--ink)}
.news-text{left:90px;top:4536px;width:560px;font-size:15px;line-height:28px}
.news-form{left:90px;top:4612px;display:flex}
.news-input{width:356px;height:50px;background:#fff;border:1px solid #dfe2e6;font-size:14px;color:#777;display:flex;align-items:center;padding-left:20px}
.news-btn{width:152px;height:50px;background:var(--blue);color:#fff;font-weight:700;font-size:16px;display:flex;align-items:center;justify-content:center}
.news-art{left:726px;top:4428px;width:340px;height:280px;border-radius:120px 140px 60px 100px;background:linear-gradient(160deg,#d9eefa,#7cc3ec)}

/* footer */
.footer{left:0;top:4774px;width:1200px;height:480px;background:var(--footer)}
.footer-curve{left:0;top:4740px;width:1200px;height:70px}
.f-brand{left:400px;top:4906px;width:400px;text-align:center;color:#fff;font-size:26px;font-weight:600}
.contact{top:5052px;display:flex;align-items:center;gap:20px;color:#fff;font-size:15px;line-height:26px}
.c-icon{width:48px;height:48px;border-radius:50%;border:2px solid #fff;display:flex;align-items:center;justify-content:center;flex:none}
.social{left:556px;top:5124px;display:flex;gap:16px}
.social i{width:20px;height:20px;border-radius:50%;background:#fff}
.f-links{left:0;top:5157px;width:1200px;text-align:center;color:#fff;font-size:14px;word-spacing:4px}
.copy{left:0;top:5196px;width:1200px;text-align:center;color:#fff;font-size:14px}
</style>
</head>
<body>

<!-- HERO -->
<div class="abs hero"></div>
<div class="abs hero-art" role="img" aria-label="Illustration of a smartphone with glowing medical icons and a stethoscope"></div>
<nav class="abs nav">
  <span class="active">Home</span><span>About Us</span><span>Services ▾</span><span>Vision</span>
  <div class="right"><span style="margin:0">Faq</span><span style="margin:0">Pages</span>
    <span class="phone"><svg width="18" height="18" viewBox="0 0 24 24"><path fill="#fff" d="M6.6 10.8a15 15 0 0 0 6.6 6.6l2.2-2.2a1 1 0 0 1 1-.25 11.4 11.4 0 0 0 3.6.57 1 1 0 0 1 1 1V20a1 1 0 0 1-1 1A17 17 0 0 1 3 4a1 1 0 0 1 1-1h3.5a1 1 0 0 1 1 1c0 1.25.2 2.45.57 3.57a1 1 0 0 1-.25 1z"/></svg>555-010-0100</span></div>
</nav>
<div class="abs brand">Brightwell Health</div>
<p class="abs hero-intro">Brightwell Health is a full-service MOBILE medical practice serving the Raleigh area in North Carolina.We come to you.</p>
<p class="abs hero-accept">Now accepting new patients <a>More</a></p>
<h1 class="abs hero-lead">We bring your doctor, laboratory, imaging suite, pharmacy &amp; personalized wellness care to your house or office.</h1>
<div class="abs btn btn-hero">Request a Visit Now</div>
<div class="abs dots"><i></i><i></i><i></i><i></i></div>
<svg class="abs hero-curve" viewBox="0 0 1200 100" preserveAspectRatio="none"><path d="M0 0 Q600 150 1200 0 V100 H0Z" fill="#fff"/></svg>

<!-- SERVICES -->
<section class="abs service" style="left:90px">
  <div class="svc-head"><div class="svc-icon"></div><h3>Primary Care at<br>Your Location</h3></div>
  <p class="svc-text">Full service direct concierge care by doctors you know and trust_ When you feel sick, no need to make a trip to the doctor's office. We come to you in the comfort of your home or office</p>
  <ul class="svc-list"><li>Preventive Care</li><li>Vaccinations/Travel Planning</li><li>Chronic Disease Management</li><li>Prescription Fulfillment</li></ul>
  <p class="svc-link">MEET THE DOCTORS »</p>
</section>
<section class="abs service" style="left:450px">
  <div class="svc-head"><div class="svc-icon"></div><h3>Urgent Care at<br>You Location</h3></div>
  <p class="svc-text">Skip the trip to the urgent care or ER if it's not necessary. We manage injuries, stitches, x-rays, chest pain, splints &amp; casts and much more</p>
  <ul class="svc-list"><li>Real-time laboratories</li><li>Real-time x-rays</li><li>Stitches/casts</li><li>Mediclions &amp; iV's</li><li>Observations</li></ul>
  <p class="svc-link">CONDITIONS WE TREAT »</p>
</section>
<section class="abs service" style="left:810px">
  <div class="svc-head"><div class="svc-icon"></div><h3>Wellness Care<br>at Your Location</h3></div>
  <p class="svc-text">No matter what your health needs are, we work with you to create a personal-ized wellness plan to help you achieve your goals for optimal health_ If leeded we will help you connect to other health resources.</p>
  <ul class="svc-list"><li>Personalized wellness care</li><li>Hormone management</li><li>IV Therapy*</li><li>Aesthetic Cosmetic</li></ul>
  <p class="svc-link">MEET THE DOCTORS »</p>
</section>

<!-- OFFER BAND -->
<svg class="abs band" viewBox="0 0 1200 530" preserveAspectRatio="none"><path d="M0 0 Q600 120 1200 10 V470 Q600 560 0 430Z" fill="#3ec3e8"/></svg>
<div class="abs band-art" role="img" aria-label="Illustration of a person marking a large calendar"></div>
<div class="abs band-text">
  <p>Now accepting new patients with full mobile care starting <strong>March 1, 2020</strong></p>
  <p>New patients will have immediate access to brightwell health mobile urgent care for <b>$50/month.</b></p>
</div>
<div class="abs prices"><span><b>$300/mo.</b> individual</span><span><b>$400/mo.</b> married couple</span><span><b>$75/ea. per mo.</b> per child with adult subscription</span></div>
<div class="abs btn btn-sub">Subscribe Today</div>

<!-- FAQ TILES -->
<div class="abs tile t1"><h3>01.How does<br>this work?</h3><a>Read More</a></div>
<div class="abs tile t2"><h3>02.When will I be<br>charged?</h3><a>Read More</a></div>
<div class="abs tile t3"><h3>03.Why should I<br>sign up now,<br>before March 1,<br>2020?</h3><a>Read More</a></div>
<div class="abs tile t4"><h3>04.How does<br>this work with<br>my insurance?</h3><a>Read More</a></div>
<svg class="abs ring" viewBox="0 0 580 570">
  <circle cx="290" cy="286" r="268" fill="none" stroke="#fff" stroke-width="14"/>
  <rect x="283" y="0" width="14" height="570" fill="#fff"/>
  <rect x="0" y="272" width="580" height="24" fill="#fff"/>
  <g fill="none" stroke="#fff" stroke-width="2.5">
    <rect x="140" y="134" width="52" height="72" rx="4"/><circle cx="166" cy="158" r="7"/><path d="M154 180h24M154 190h16"/><circle cx="194" cy="200" r="12"/><path d="M188 200l4 4 8-8"/>
    <rect x="368" y="130" width="58" height="84" rx="6"/><path d="M378 150l4 4 6-7M394 152h22M378 172l4 4 6-7M394 174h22M378 194l4 4 6-7M394 196h22"/>
    <rect x="140" y="344" width="52" height="70" rx="4"/><circle cx="158" cy="358" r="6"/><path d="M150 376h18M150 390h28M150 402h22M182 404l22-22 6 6-22 22h-6z"/>
    <path d="M384 352l24 10v16c0 18-12 28-24 34-12-6-24-16-24-34v-16z"/><path d="M384 370v22M373 381h22"/><rect x="412" y="350" width="30" height="62" rx="3"/><path d="M420 366h14M420 380h14M420 394h14"/>
  </g>
</svg>

<!-- WHY -->
<svg class="abs why-bg" viewBox="0 0 1200 1210" preserveAspectRatio="none"><path d="M0 40 Q600 -40 1200 40 V1170 Q600 1240 0 1170Z" fill="#eef8fc"/></svg>
<h2 class="abs why-title">Why brightwell <span>HEALTH</span>?</h2>
<div class="abs why-art-a" role="img" aria-label="Illustration of a doctor beside a large digital health record screen"></div>
<div class="abs why-art-b" role="img" aria-label="Illustration of a medical team in front of a shield with a cross"></div>

<div class="abs item" style="left:552px;top:2792px"><span class="num">01.</span><h4>No drive to the doctor when you're sick...</h4><p>the last thing you want to do when you don't feel good is make the trip to the doctor's office. We come to you in the comfort of your own home or office.</p></div>
<div class="abs item" style="left:552px;top:2928px"><span class="num">02.</span><h4>Forget crowded waiting rooms filled with germs...</h4><p>we provide all of your care in your home or office, clean and easy.</p></div>
<div class="abs item" style="left:552px;top:3010px"><span class="num">03.</span><h4>Skip the trip to the ER or urgent care...</h4><p>we come to you and deliver high-level care and our team has extensive experience in the emergency room so we're prepared to handle most medical issues. We'll tell you when you should go to the ER because we'll be talking to you as we are traveling to you.</p></div>
<div class="abs item" style="left:552px;top:3168px"><span class="num">04.</span><h4>Avoid the 4 hour wait...</h4><p>We can be at most folks' home within an hour of request, or, better yet, for non-urgent situations, schedule at your convenience when you would like us to care for you.</p></div>
<div class="abs item" style="left:90px;top:3322px"><span class="num">05.</span><h4>No more 5 pages of forms...</h4><p>We do all the paperwork for you and keep it on file for next time.</p></div>
<div class="abs item" style="left:90px;top:3404px"><span class="num">06.</span><h4>Know your doctor and care team!</h4><p>You will see familiar faces who know your health history and who are on your team toward health and wellness. We are physicians and clinicians who are experienced in primary, urgent and emergency care. We go way beyond sick visits and can handle most urgent and emergent situations so that you do not have to leave your home.</p></div>
<div class="abs item" style="left:90px;top:3594px"><span class="num">07.</span><h4>We're available for extended hours...</h4><p>Doesn't it seem that we always need a doctor on Friday<br>night or the weekend? We come to you between 8 am and 8 pm<br>seven days a week.</p></div>

<!-- PROVIDERS -->
<h2 class="abs prov-title">brightwell HEALTH <span class="accent">medical providers</span></h2>
<div class="abs prov" style="left:90px"><div class="ph" role="img" aria-label="Portrait illustration of a provider"></div><p>Dr.Lane</p></div>
<div class="abs prov" style="left:300px"><div class="ph" role="img" aria-label="Portrait illustration of a provider"></div><p>Dr.Reed</p></div>
<div class="abs prov" style="left:509px"><div class="ph" role="img" aria-label="Portrait illustration of a provider"></div><p>Owen,PA</p></div>
<div class="abs prov" style="left:718px"><div class="ph" role="img" aria-label="Portrait illustration of a provider"></div><p>Mara,PA</p></div>
<div class="abs prov" style="left:928px"><div class="ph" role="img" aria-label="Portrait illustration of a provider"></div><p>Tess,PA</p></div>

<!-- NEWSLETTER -->
<svg class="abs news-bg" viewBox="0 0 1200 450" preserveAspectRatio="none"><path d="M0 40 Q600 -30 1200 40 V450 H0Z" fill="#f2f3f5"/></svg>
<div class="abs news-art" role="img" aria-label="Illustration of people walking through open doors among plants"></div>
<h2 class="abs news-title">Subscribe <span class="accent">Our Newsletter</span></h2>
<p class="abs news-text">Lorem ipsum dolor sit amet, consectetur adipiscing elit, sed do eiusmod tempor incididunt ut labore et dolore magna aliqua.</p>
<div class="abs news-form"><div class="news-input">Enter Your Email Address</div><div class="news-btn">SUBSCRIBE</div></div>

<!-- FOOTER -->
<div class="abs footer"></div>
<svg class="abs footer-curve" viewBox="0 0 1200 70" preserveAspectRatio="none"><path d="M0 34 Q600 -20 1200 34 V70 H0Z" fill="#1b1e24"/></svg>
<div class="abs f-brand">Brightwell Health</div>
<div class="abs contact" style="left:90px"><span class="c-icon"><svg width="18" height="22" viewBox="0 0 24 30"><path d="M12 2a9 9 0 0 0-9 9c0 7 9 17 9 17s9-10 9-17a9 9 0 0 0-9-9z" fill="none" stroke="#fff" stroke-width="2.5"/><circle cx="12" cy="11" r="3.5" fill="#fff"/></svg></span><span>24 Larkfield Rd, Westbrook<br>Park 4120</span></div>
<div class="abs contact" style="left:504px"><span class="c-icon"><svg width="20" height="20" viewBox="0 0 24 24"><path fill="#fff" d="M6.6 10.8a15 15 0 0 0 6.6 6.6l2.2-2.2a1 1 0 0 1 1-.25 11.4 11.4 0 0 0 3.6.57 1 1 0 0 1 1 1V20a1 1 0 0 1-1 1A17 17 0 0 1 3 4a1 1 0 0 1 1-1h3.5a1 1 0 0 1 1 1c0 1.25.2 2.45.57 3.57a1 1 0 0 1-.25 1z"/></svg></span><span>Phone :<br>555-010-0100</span></div>
<div class="abs contact" style="left:818px"><span class="c-icon"><svg width="22" height="16" viewBox="0 0 24 18"><rect x="1.5" y="1.5" width="21" height="15" rx="2" fill="none" stroke="#fff" stroke-width="2"/><path d="M2 3l10 7 10-7" fill="none" stroke="#fff" stroke-width="2"/></svg></span><span>E - Mail :<br>hello@brightwell.example</span></div>
<div class="abs social"><i></i><i></i><i></i></div>
<p class="abs f-links">Home &nbsp;|&nbsp; About Use &nbsp;|&nbsp; Servicese &nbsp;|&nbsp; Visione &nbsp;|&nbsp; Faqe &nbsp;|&nbsp; Pages</p>
<p class="abs copy">Copyright © 2019.All Rights Reserved.</p>

</body>
</html>
```